4th Generation Family Business Needs a New Card Design!

We are a family owned 4th Generation company. We are based in the Sydney, Australia area and we are desperately in need of a more modern and classy card. We are monumental masons who design, supply & erect lasting memorials throughout cemeteries in Sydney. Our customers are normally in a period of grieving. I have attached logo files that will need to be implemented on the card. Company was established 1935. Australian Owned and Operated. Card needs to be designed to PIXO.com specification.

Target Market(s)

Our target market is based upon people that a grieving for family members that have passed away. We also deal with alot of companies that own and operate cemeteries.

Industry/Entity Type

Business

Contact Information for Business Card

Simon Harcourt, Operations Manager, 0417293086, simon@harcourtmemorials.com.au
Lewis Harcourt, Director, 0491630572, lewis@harcourtmemorials.com.au
Phone # 02 9561 3048
Website: www.harcourtmemorials.com.au
Address: Suite 17, 8 Palfrey Lane, West Carlow, Sydney NSW 2156

Font styles to use
Serif
Decorative
Script

Requirements
Must have
• Would like to see the logo nicely implemented with a modern design. Embossed lettering would be a nice additive.

```html
<!DOCTYPE html>
<html lang="en">
<head>
<meta charset="utf-8">
<title>Harcourt Memorials – Business Card</title>
<link rel="stylesheet" href="https://fonts.googleapis.com/css2?family=Cinzel:wght@400;600&family=Tinos&display=swap">
<style>
  :root {
    --backdrop: #dcdcdc;
    --card: #f7f7f7;
    --ink: #1a1a1a;
    --ink-soft: #333333;
    --gold: #d4ac1f;
    --black-band: #0e0e0e;
  }
  * { margin: 0; padding: 0; box-sizing: border-box; }
  html, body { width: 1200px; height: 576px; overflow: hidden; }
  body {
    background: var(--backdrop);
    position: relative;
    font-family: "Tinos", "Times New Roman", serif;
    color: var(--ink);
  }
  .card {
    position: absolute;
    background: var(--card);
    overflow: hidden;
  }
  .card-front { left: 80px; top: 138px; width: 486px; height: 294px; }
  .card-back  { left: 602px; top: 138px; width: 481px; height: 292px; }

  .front-band {
    position: absolute; left: 0; right: 0; bottom: 0; height: 10px;
    background: var(--gold);
  }
  .brand-name {
    font-family: "Cinzel", "Times New Roman", serif;
    font-weight: 600;
    color: var(--ink);
    text-align: center;
    line-height: 1;
  }
  .front-brand {
    position: absolute; left: 0; right: 0; top: 112px;
    font-size: 34px;
  }
  .front-brand .brand-sub { display: block; font-size: 15px; letter-spacing: 2px; margin-top: 8px; }

  .back-bar { position: absolute; left: 0; top: 0; bottom: 0; width: 41px; background: var(--black-band); }
  .back-stripe { position: absolute; left: 41px; top: 0; bottom: 0; width: 5px; background: var(--gold); }

  .holder { position: absolute; left: 62px; top: 28px; }
  .holder-name {
    font-family: "Cinzel", "Times New Roman", serif;
    font-weight: 600; font-size: 19px; color: var(--ink);
  }
  .holder-role { font-size: 11px; margin-top: 2px; color: var(--ink-soft); }

  .back-brand {
    position: absolute; left: 290px; width: 180px; top: 94px;
    font-size: 22px;
  }
  .back-brand .brand-sub { display: block; font-size: 11px; letter-spacing: 1.5px; margin-top: 5px; }

  .contact-list {
    position: absolute; left: 62px; top: 188px;
    list-style: none; font-size: 12px; line-height: 18px;
  }
  .contact-list li { display: flex; align-items: center; }
  .contact-icon { width: 10px; height: 10px; margin-right: 12px; fill: var(--gold); }
  .address { position: absolute; left: 62px; top: 262px; font-size: 12px; color: var(--ink-soft); }
</style>
</head>
<body>
  <section class="card card-front">
    <div class="brand-name front-brand">Harcourt<span class="brand-sub">Memorials</span></div>
    <div class="front-band"></div>
  </section>

  <section class="card card-back">
    <div class="back-bar"></div>
    <div class="back-stripe"></div>

    <div class="holder">
      <div class="holder-name">Simon Harcourt</div>
      <div class="holder-role">Operations Manager</div>
    </div>

    <div class="brand-name back-brand">Harcourt<span class="brand-sub">Memorials</span></div>

    <ul class="contact-list">
      <li><svg class="contact-icon" viewBox="0 0 10 10"><path d="M2 0.5l2 2-1 1.2c.6 1.3 1.6 2.3 2.9 2.9l1.2-1 2 2-1.3 1.6C4.2 9 1 5.8.4 1.9z"/></svg>0491630572</li>
      <li><svg class="contact-icon" viewBox="0 0 10 10"><path d="M0 3.2C0 1.5 2.5 1 5 1s5 .5 5 2.2V4H7.4V3H2.6v1H0z M1.5 5h7l1 4h-9z"/></svg>02 9561 3048</li>
      <li><svg class="contact-icon" viewBox="0 0 10 10"><path d="M0 2h10v.8L5 5.8 0 2.8z M0 3.9l5 3 5-3V8H0z"/></svg>lewis@harcourtmemorials.com.au</li>
      <li><svg class="contact-icon" viewBox="0 0 10 10"><circle cx="5" cy="5" r="4.5"/><path d="M.5 5h9M5 .5v9" stroke="#f7f7f7" stroke-width=".8"/></svg>www.harcourtmemorials.com.au</li>
    </ul>
    <div class="address">Suite 17, 8 Palfrey Lane, West Carlow, Sydney NSW 2156</div>
  </section>
</body>
</html>
```